Business Card Design

We need a business card designed for our new company. Prefer a black card with white logo & writing.

Contact Information for Business Card

Ted Galloway, address: 7-4812 Fernhollow Road, Abbotsford, BC, V3K 8R2, Office Phone: 604-712-3390, Cell: 604-947-2164, Email: ted@resinworkshub.ca

Colors

Designer to choose only greyscale colors for use in the design.

```html
<!DOCTYPE html>
<html lang="en">
<head>
<meta charset="utf-8">
<title>Resin Works Hub – Business Card</title>
<link href="https://fonts.googleapis.com/css2?family=Montserrat:wght@400;700&display=swap" rel="stylesheet">
<style>
  :root {
    --backdrop: #3a3633;
    --card: #0f0f0f;
    --ink: #ffffff;
    --ink-soft: #e6e6e6;
    --grey-light: #d4d4d4;
    --grey-mid: #9a9a9a;
    --grey-dark: #5c5c5c;
  }
  * { box-sizing: border-box; margin: 0; padding: 0; }
  html, body {
    width: 1200px; height: 786px; overflow: hidden;
    background: var(--backdrop);
    font-family: "Montserrat", sans-serif;
    color: var(--ink);
  }
  .canvas {
    position: relative; width: 1200px; height: 786px;
    display: flex; align-items: center; justify-content: center; gap: 40px;
  }
  .card {
    position: relative; width: 540px; height: 309px;
    background: var(--card);
    box-shadow: 0 12px 30px rgba(0,0,0,.45);
  }
  /* Front: contact side */
  .contact-brand {
    position: absolute; left: 34px; top: 34px;
    font-weight: 700; font-size: 19px; letter-spacing: .5px; line-height: 1.1;
  }
  .contact-name {
    position: absolute; left: 34px; top: 98px;
    font-weight: 700; font-size: 24px;
  }
  .contact-address {
    position: absolute; left: 34px; top: 144px;
    font-size: 13.5px; line-height: 1.5; color: var(--ink-soft);
  }
  .contact-list {
    position: absolute; left: 34px; top: 200px; list-style: none;
    font-size: 13.5px; line-height: 1.6; color: var(--ink-soft);
  }
  .contact-list li { display: flex; align-items: center; gap: 8px; }
  .contact-list svg { width: 13px; height: 13px; fill: none; stroke: var(--ink); stroke-width: 1.6; }
  .contact-list .no-icon { padding-left: 21px; }
  .emblem {
    position: absolute; right: 50px; top: 50%; transform: translateY(-50%);
    width: 210px; height: 210px; border-radius: 50%;
    background: var(--ink);
    display: flex; align-items: center; justify-content: center;
  }
  .emblem-fill {
    width: 150px; height: 120px; border-radius: 6px;
    background: linear-gradient(160deg, var(--grey-light), var(--grey-mid) 55%, var(--grey-dark));
  }
  /* Back: brand side */
  .brand-side { display: flex; align-items: center; justify-content: center; }
  .brand-name {
    font-weight: 700; font-size: 34px; letter-spacing: 1px; text-align: center; line-height: 1.1;
  }
</style>
</head>
<body>
  <main class="canvas">
    <section class="card contact-side">
      <p class="contact-brand">RESIN WORKS<br>HUB</p>
      <h1 class="contact-name">Ted Galloway</h1>
      <p class="contact-address">7-4812 Fernhollow Road,<br>Abbotsford, BC, V3K 8R2</p>
      <ul class="contact-list">
        <li class="no-icon">604-712-3390</li>
        <li>
          <svg viewBox="0 0 16 16" aria-hidden="true"><path d="M4 2l2.5 3-1.5 1.5a8 8 0 0 0 4.5 4.5L11 9.5 14 12l-1.5 2C7 14 2 9 2 3.5z"/></svg>
          604-947-2164
        </li>
        <li>
          <svg viewBox="0 0 16 16" aria-hidden="true"><rect x="1.5" y="3.5" width="13" height="9"/><path d="M1.5 3.5L8 9l6.5-5.5"/></svg>
          ted@resinworkshub.ca
        </li>
        <li>
          <svg viewBox="0 0 16 16" aria-hidden="true"><circle cx="8" cy="8" r="6.5"/><path d="M1.5 8h13M8 1.5c-3 3.5-3 9.5 0 13M8 1.5c3 3.5 3 9.5 0 13"/></svg>
          resinworkshub.ca
        </li>
      </ul>
      <div class="emblem">
        <div class="emblem-fill" role="img" aria-label="Illustration of stacked floor coating layers in greys"></div>
      </div>
    </section>
    <section class="card brand-side">
      <p class="brand-name">RESIN WORKS<br>HUB</p>
    </section>
  </main>
</body>
</html>
```